Flyer für Veranstaltungstechnik-Unternehmen
Zielgruppe
VERANSTALTUNGSTECHNIK
Aufgabenstellung
Wir haben diesen Flyer erhalten, finden ihn aber nicht ansprechend, sehr altmodisch und möchten einen klar strukturierten modernen Flyer.
DIN A5 „Heft“ – Und das Profil als „Einleger“. Sollte dementsprechend ca. 1 cm umlaufend kleiner sein.
Der Flyer soll sich an dem Design der Webseite orientieren!

```html
<!DOCTYPE html>
<html lang="de">
<head>
<meta charset="utf-8">
<title>Lumavent – Leistungen</title>
<link href="https://fonts.googleapis.com/css2?family=Red+Hat+Display:wght@300;400;700&display=swap" rel="stylesheet">
<style>
  :root {
    --purple: #9b86bf;
    --lilac-bg: #e9e5f1;
    --ink: #1f1d24;
    --white: #ffffff;
    --footer-light: #d8d8d8;
  }
  * { margin: 0; padding: 0; box-sizing: border-box; }
  html, body { width: 1200px; height: 822px; overflow: hidden; }
  body { font-family: "Red Hat Display", Arial, sans-serif; color: var(--ink); background: var(--white); }
  .spread { position: relative; width: 1200px; height: 822px; display: flex; }
  .page { position: relative; width: 600px; height: 822px; overflow: hidden; }
  .page--left { background: var(--white); }
  .page--right { background: var(--lilac-bg); }

  .section-tag {
    position: absolute; top: 69px; height: 36px;
    padding: 0 12px; background: var(--purple); border-radius: 6px;
    color: var(--white); font-size: 23.5px; line-height: 36px; font-weight: 300; letter-spacing: 0.2px;
    white-space: nowrap;
  }
  .page--left .section-tag { left: 56px; }
  .page--right .section-tag { left: 56px; }
  .section-tag strong { font-weight: 700; }

  .intro { position: absolute; top: 127px; left: 56px; width: 490px; }
  .intro p { font-size: 16.8px; line-height: 19.7px; font-weight: 300; margin-bottom: 15px; hyphens: manual; }

  .hero-photo {
    position: absolute; left: 0; top: 527px; width: 600px; height: 295px;
    background: radial-gradient(ellipse at 30% 30%, #6b6b6b 0%, #3a3a3a 35%, #141414 75%, #050505 100%);
  }
  .offer-box {
    position: absolute; left: 189px; top: 503px; width: 355px; height: 208px;
    background: var(--purple); border-radius: 11px; padding: 19px 14px 0 21px;
    color: var(--white); font-size: 16px; line-height: 18.6px; font-weight: 400;
  }

  .glance-list { position: absolute; top: 127px; left: 37px; width: 500px; list-style: none; }
  .glance-list li {
    position: relative; padding-left: 11px; margin-bottom: 5.6px;
    font-size: 16.8px; line-height: 19.4px; font-weight: 300;
  }
  .glance-list li::before { content: "•"; position: absolute; left: 0; top: 0; font-size: 12px; }

  .web-tag {
    position: absolute; top: 731px; left: 56px; width: 211px; height: 35px;
    background: var(--purple); border-radius: 6px; color: var(--white);
    font-size: 15.5px; line-height: 35px; text-align: center; font-weight: 400;
  }
  .web-rule { position: absolute; top: 748px; left: 267px; width: 333px; height: 2px; background: var(--purple); }

  .folio { position: absolute; top: 777px; font-size: 12.5px; font-weight: 300; }
  .folio--left { left: 40px; color: var(--footer-light); }
  .folio--right { right: 41px; color: var(--ink); }
</style>
</head>
<body>
<div class="spread">
  <section class="page page--left">
    <h2 class="section-tag"><strong>LEIST</strong>UNGEN</h2>
    <div class="intro">
      <p>Dank der Erfahrung und Kompetenz unseres Fachpersonals können wir technische Zeichnungen sowie Veranstaltungs-, Sicherheits- und Brandschutzkonzepte maßgeschneidert für Ihre Veranstaltung erstellen und umsetzen.</p>
      <p>Unser Event-Team begleitet Sie in allen Phasen Ihrer Veranstaltung, berät Sie in allen Fachbereichen und übernimmt auf Wunsch auch die Prüfung von Verträgen und Rechnungen externer Dienstleister. Selbstverständlich sind Ihre vertraulichen Daten bei uns in guten Händen.</p>
      <p>Als Experten auf dem Gebiet der Veranstaltungstechnik und Event­planung begleiten wir Sie in allen Belangen Ihrer Veranstaltung und bieten Ihnen neben der technischen Planung auch hochqualifiziertes Fachpersonal: Veranstaltungstechniker:innen, Eventmanager:innen, Projektleiter:innen bis hin zu Meister:innen für Veranstaltungstechnik, Elektrotechniker:innen und Lichtpultoperatoren.</p>
    </div>
    <div class="hero-photo" role="img" aria-label="Schwarzweißfoto eines Mischpults mit Fadern und Reglern"></div>
    <div class="offer-box">Wir bieten unter anderem die Bereitstellung von individuellen Traversen- und Beleuch­tungskonstruktionen sowie mobilen und stationären Stromanschlüssen, Logistik- und Transportleistungen, Fachpersonal mit allen branchenüblichen Berechtigungen, die Durchführung von Baunebenleistungen und die Unterstützung bei der Durchführung von Genehmigungsverfahren.</div>
    <div class="folio folio--left">4&nbsp;&nbsp;|&nbsp;&nbsp;Lumavent</div>
  </section>

  <section class="page page--right">
    <h2 class="section-tag"><strong>AUF EINEN</strong> BLICK</h2>
    <ul class="glance-list">
      <li>Vorplanung, Durchführung und Nachbereitung<br>von Veranstaltungen</li>
      <li>Koordination, Organisation und Planung sämtlicher Gewerke</li>
      <li>Erstellen von Projekt-, Budget- und Terminplänen</li>
      <li>Budgetierung aller Bereiche und Gewerke, auch auf Kunden­seite und damit verbunden die Prüfung aller Verträge, Angebote und Rechnungen im Rahmen der Veranstaltungen (Third Party Audit)</li>
      <li>Kommunikation mit allen Gewerken, der Location<br>und den Behörden</li>
      <li>Erstellen von Sicherheitskonzepten unter Einbeziehung von Sicherheitspersonal</li>
      <li>Erstellung von Gefährdungsbeurteilungen für die zu<br>betreuenden technischen Bereiche</li>
      <li>Koordination, Abstimmung und Übernahme der logistischen Verantwortung für den Messebereich</li>
      <li>Übernahme des Verantwortlichen für Veranstaltungstechnik (Meister für Veranstaltungstechnik)</li>
      <li>Übernahme der Verantwortung als technischer Leiter für die Gesamtveranstaltung</li>
      <li>Studioumbauten und Betreuung</li>
      <li>Technische Betreuung Bühne und Licht</li>
      <li>Koordination Dekorationsbau</li>
      <li>Zeichnen aller veranstaltungsspezifischen Pläne<br>(technisch und sicherheitstechnisch)</li>
    </ul>
    <div class="web-tag">www.lumavent-event.de</div>
    <div class="web-rule"></div>
    <div class="folio folio--right">Lumavent&nbsp;&nbsp;|&nbsp;&nbsp;5</div>
  </section>
</div>
</body>
</html>
```